Powerpoint design template for LUMOTEX for new digital platform

We would like to use a PowerPoint template, we would like to create a new page, we would like to create a new digital platform LUMOTEX for schools and parents for the creation of playful communication and educational tools for children to enhance their positive development, amaze them learn in a playful way. This platform is going to be the most creative, stimulating and innovative classroom, easy to use and fast to implement. Scrapbooking, collages ... Magazine, newsletters Diplomla / awards Slideshows Facebook Calendars Organizers Greetings Games ... This powerpoint template will be used essential to We are looking for a professional design, positioning our brand in the children market with an adult hearing. so you will need to find a good deal. Primary target: nurseries & schools from 0 to 18 years old and universities (in 2nd phase) Secondary target: small & medium businesses Third target: general public, and TPE If it is a color scheme, then it is suggested that it be marketed in Europe (UK, Italy, Spain) and in a 2nd Stage USA and other countries. multiple options for front page, insidious pages (multiple styles with limited text and extended text) and final contact page We need something to read, we can not do it too much, but we can not do it. , and inside pages aligned to our logo

Target Market(s)

Target 1; Education with teacher Target 2; parents and grandparents

Industry/Entity Type

Education

Font styles to use
Other font styles liked:
• not decided. but not too fancy

Requirements
Must have
• Multi page options for front page, page insides (multiple styles with limited text and extended text) and final page contact
Nice to have
• do not have a lot of ideas. We need something to read, we can not get away from it
Should not have
• not too fancy and busy: keep clarity & simplicity while reassuring on quality

```html
<!DOCTYPE html>
<html lang="en">
<head>
<meta charset="utf-8">
<title>Project Title Here – LUMOTEX</title>
<link rel="stylesheet" href="https://fonts.googleapis.com/css2?family=Roboto+Condensed:wght@700&family=Roboto:wght@400;500;700&display=swap">
<style>
  :root{
    --lime:#d6e03f;
    --lime-light:#e6ec7a;
    --green:#a9c938;
    --green-dark:#7fb13a;
    --orange:#f7941d;
    --ink:#2b2b2b;
    --heading:#333333;
    --body:#6a6a6a;
    --blue:#00aeef;
    --magenta:#cc1fb4;
    --yellow:#ffc20e;
    --teal:#2ee6c6;
    --white:#ffffff;
  }
  *{margin:0;padding:0;box-sizing:border-box}
  html,body{width:1200px;height:900px;overflow:hidden;background:var(--white)}
  .slide{position:relative;width:1200px;height:900px;overflow:hidden;font-family:"Roboto",Arial,sans-serif;background:var(--white)}

  .header-shape{position:absolute;left:0;top:0;width:1200px;height:130px}
  .slide-title{position:absolute;left:28px;top:30px;font-family:"Roboto Condensed","Arial Narrow",sans-serif;font-weight:700;font-size:50px;letter-spacing:0.5px;color:var(--ink);line-height:1}

  .brand{position:absolute;left:995px;top:40px;display:flex;align-items:center;gap:7px}
  .brand-mark{width:16px;height:16px;background:var(--magenta)}
  .brand-name{font-family:"Roboto",Arial,sans-serif;font-weight:700;font-size:28px;color:var(--ink);line-height:1;letter-spacing:1px}
  .brand-tagline{position:absolute;left:998px;top:78px;font-size:9px;font-weight:500;letter-spacing:2px;line-height:12px;color:var(--ink);text-transform:uppercase}

  .topic{position:absolute;left:0;width:1200px;height:106px}
  .topic-tab{position:absolute;left:0;top:0;width:177px;height:106px}
  .topic-title{position:absolute;left:201px;top:0;font-weight:500;font-size:24px;color:var(--heading);line-height:28px}
  .topic-text{position:absolute;left:201px;top:34px;width:938px;font-size:16.4px;line-height:25px;word-spacing:2.5px;color:var(--body)}

  .topic--creative{top:188px}
  .topic--sales{top:339px}
  .topic--global{top:492px}
  .topic--business{top:645px}

  .footer-shape{position:absolute;left:0;top:834px;width:1200px;height:66px}
  .site-address{position:absolute;left:21px;top:853px;font-size:22px;color:var(--ink);line-height:1}
  .page-number{position:absolute;left:1077px;top:855px;font-size:21px;color:var(--ink);line-height:1}
</style>
</head>
<body>
<main class="slide">

  <svg class="header-shape" viewBox="0 0 1200 130" aria-hidden="true">
    <polygon points="0,0 985,0 900,108 0,108" fill="var(--lime)"/>
    <polygon points="930,0 985,0 900,108 870,108" fill="var(--lime-light)"/>
    <polygon points="955,0 1040,0 960,108 905,108" fill="var(--green)" opacity="0.55"/>
    <polygon points="985,12 1160,0 1180,110 1010,122" fill="var(--green-dark)" opacity="0.35"/>
    <polygon points="978,8 1155,4 1170,104 995,114" fill="var(--white)"/>
  </svg>
  <h1 class="slide-title">PROJECT TITLE HERE</h1>
  <div class="brand">
    <span class="brand-mark"></span>
    <span class="brand-name">LUMOTEX</span>
  </div>
  <p class="brand-tagline">Your tagline<br>goes here</p>

  <section class="topic topic--creative">
    <svg class="topic-tab" viewBox="0 0 177 106" aria-hidden="true">
      <polygon points="0,0 150,0 177,53 150,106 0,106" fill="var(--blue)"/>
      <rect x="46" y="30" width="48" height="34" rx="3" fill="none" stroke="var(--white)" stroke-width="5"/>
      <rect x="66" y="64" width="8" height="8" fill="var(--white)"/>
      <rect x="56" y="72" width="28" height="5" rx="1" fill="var(--white)"/>
    </svg>
    <h2 class="topic-title">Creative Strategy</h2>
    <p class="topic-text">Toffee caramels candy canes bonbon bonbon soufflé bonbon wafer. Topping I love halvah I love. Jujubes lemon drops I love jelly pie chocolate bar. Biscuit oat cake carrot cake. Muffin jelly beans chocolate chocolate. Sugar plum I love cheesecake marshmallow toffee cake sweet cookies topping jelly gummies.</p>
  </section>

  <section class="topic topic--sales">
    <svg class="topic-tab" viewBox="0 0 177 106" aria-hidden="true">
      <polygon points="0,0 150,0 177,53 150,106 0,106" fill="var(--magenta)"/>
      <path d="M88,30 C78,32 68,42 62,56 L70,64 C84,58 94,48 96,38 Z" fill="var(--white)"/>
      <path d="M62,48 L52,50 L48,58 L58,57 Z M78,68 L76,78 L68,82 L69,72 Z" fill="var(--white)"/>
      <path d="M58,66 L50,78 L62,70 Z" fill="var(--white)"/>
    </svg>
    <h2 class="topic-title">Boost Sales</h2>
    <p class="topic-text">Toffee caramels candy canes bonbon bonbon soufflé bonbon wafer. Topping I love halvah I love. Jujubes lemon drops I love jelly pie chocolate bar. Biscuit oat cake carrot cake. Muffin jelly beans chocolate chocolate. Sugar plum I love cheesecake marshmallow toffee cake sweet cookies topping jelly gummies.</p>
  </section>

  <section class="topic topic--global">
    <svg class="topic-tab" viewBox="0 0 177 106" aria-hidden="true">
      <polygon points="0,0 150,0 177,53 150,106 0,106" fill="var(--yellow)"/>
      <path d="M46,36 H64 V54 C64,66 58,72 48,74 V66 C53,65 55,61 55,56 H46 Z" fill="var(--white)"/>
      <path d="M72,36 H90 V54 C90,66 84,72 74,74 V66 C79,65 81,61 81,56 H72 Z" fill="var(--white)"/>
    </svg>
    <h2 class="topic-title">Global Brand Strategy</h2>
    <p class="topic-text">Toffee caramels candy canes bonbon bonbon soufflé bonbon wafer. Topping I love halvah I love. Jujubes lemon drops I love jelly pie chocolate bar. Biscuit oat cake carrot cake. Muffin jelly beans chocolate chocolate. Sugar plum I love cheesecake marshmallow toffee cake sweet cookies topping jelly gummies.</p>
  </section>

  <section class="topic topic--business">
    <svg class="topic-tab" viewBox="0 0 177 106" aria-hidden="true">
      <polygon points="0,0 150,0 177,53 150,106 0,106" fill="var(--teal)"/>
      <path d="M52,32 H88 V58 C88,68 80,75 70,80 C60,75 52,68 52,58 Z" fill="var(--white)"/>
      <path d="M60,39 H70 V70 C64,66 60,62 60,57 Z" fill="var(--teal)"/>
    </svg>
    <h2 class="topic-title">Business Strategy</h2>
    <p class="topic-text">Toffee caramels candy canes bonbon bonbon soufflé bonbon wafer. Topping I love halvah I love. Jujubes lemon drops I love jelly pie chocolate bar. Biscuit oat cake carrot cake. Muffin jelly beans chocolate chocolate. Sugar plum I love cheesecake marshmallow toffee cake sweet cookies topping jelly gummies.</p>
  </section>

  <svg class="footer-shape" viewBox="0 0 1200 66" aria-hidden="true">
    <rect x="0" y="0" width="1200" height="66" fill="var(--lime)"/>
    <polygon points="975,0 1000,0 1050,66 1020,66" fill="var(--green)"/>
    <polygon points="995,0 1200,0 1200,66 1050,66" fill="var(--green-dark)" opacity="0.6"/>
    <polygon points="1005,0 1200,0 1200,66 1060,66" fill="var(--orange)"/>
  </svg>
  <p class="site-address">www.lumotex.com</p>
  <p class="page-number">Page : 01</p>

</main>
</body>
</html>
```